Interval Timer App

Need to have design for the attached wireframe. Similar app can be found here: https://shop.lumaverse.net/store/apps/details?id=cc.quillfern.pulseclock

```html
<!DOCTYPE html>
<html lang="en">
<head>
<meta charset="UTF-8">
<title>Interval Timer – Rest</title>
<link href="https://fonts.googleapis.com/css2?family=Open+Sans:wght@400;600;700&display=swap" rel="stylesheet">
<style>
  :root {
    --sky-top: #5ff0fb;
    --sky-bottom: #0bc4f8;
    --brand-blue: #1a7fe3;
    --ink: #1f2230;
    --card: #ffffff;
    --track: #ffffff;
  }
  * { margin: 0; padding: 0; box-sizing: border-box; }
  html, body { width: 675px; height: 1200px; overflow: hidden; }
  body {
    position: relative;
    font-family: "Open Sans", sans-serif;
    background: linear-gradient(180deg, var(--sky-top) 0%, var(--sky-bottom) 100%);
  }
  .back-button { position: absolute; left: 30px; top: 38px; width: 34px; height: 38px; }
  .set-progress { position: absolute; left: 195px; top: 166px; width: 287px; }
  .set-label {
    text-align: center; font-size: 22px; color: var(--ink);
    letter-spacing: 0.5px; margin-left: 0; width: 248px;
  }
  .progress-track {
    position: relative; margin-top: 14px; height: 5px; width: 287px;
    background: var(--track); border-radius: 3px;
  }
  .progress-fill {
    position: absolute; left: 0; top: 0; height: 5px; width: 124px;
    background: var(--brand-blue); border-radius: 3px;
  }
  .progress-knob {
    position: absolute; left: 113px; top: -9px; width: 23px; height: 23px;
    border-radius: 50%; background: #fff; border: 3px solid var(--brand-blue);
  }
  .rest-card {
    position: absolute; left: 30px; top: 281px; width: 615px; height: 638px;
    background: var(--card); border-radius: 18px;
  }
  .rest-title {
    position: absolute; top: 47px; width: 100%; text-align: center;
    font-size: 40px; font-weight: 400; color: var(--ink);
  }
  .timer-ring { position: absolute; left: 0; top: 0; }
  .timer-value {
    position: absolute; left: 141px; top: 272px; width: 300px; text-align: center;
    font-size: 90px; font-weight: 600; color: var(--brand-blue); line-height: 1.2;
  }
  .skip-button {
    position: absolute; left: 186px; top: 533px; width: 243px; height: 75px;
    border-radius: 38px; background: var(--brand-blue); color: #fff;
    font-family: "Open Sans", sans-serif; font-size: 24px; font-weight: 600;
    letter-spacing: 1px; border: none; display: flex; align-items: center; justify-content: center;
  }
</style>
</head>
<body>
  <svg class="back-button" viewBox="0 0 34 38" aria-label="Back">
    <polyline points="24,4 9,19 24,34" fill="none" stroke="#1a7fe3" stroke-width="4.5" stroke-linecap="round" stroke-linejoin="round"/>
  </svg>

  <div class="set-progress">
    <div class="set-label">SET 1</div>
    <div class="progress-track">
      <div class="progress-fill"></div>
      <div class="progress-knob"></div>
    </div>
  </div>

  <section class="rest-card">
    <h1 class="rest-title">Rest time!</h1>
    <svg class="timer-ring" width="615" height="638" viewBox="0 0 615 638" aria-hidden="true">
      <path d="M300 171 A167 167 0 0 1 458 338" fill="none" stroke="var(--ink)" stroke-width="4.5" stroke-linecap="round"/>
      <circle cx="458" cy="338" r="14" fill="var(--brand-blue)"/>
    </svg>
    <div class="timer-value">0:30</div>
    <button class="skip-button">SKIP</button>
  </section>
</body>
</html>
```